Progressive European Honey Business needs minimalistic packaging design

Hello - thank you for your interest in our brief. We are Honey Plinks, a London based Honey business, importing only the best honey Europe has to offer. Our values are deeply rooted with in progressive liberal values and we are looking for minimalist packaging, which reflects that.

We are looking for a design, which dimensions fit with our packaging option (Vessio Glass Jar | HEIGHT 90mm | DIAMETER 63mm). We will require a various output files (High Resolution JPEG (CMYK Colors 300 dpi) Source File Ai, PSD, PDF, Printing files (die cut, die folding) and a 3D Mockup of the packaging for use within digital commerce platforms.

We must be able to adjust the free text on the label front and it should include the following:
Brand Name
Honey type
Limited edition No. X / 100 ( X being the number of purchase i.e. 25 / 100)
EU Honey, Single Orgin (Germany)
(c) The net weight (250g)

The back must include room for additional information (again adjustable by us) and the following:
“Unsuitable for children under 12 months”
(b) The appropriate durability declaration

In total, we are looking for
a) A front label
b) A back label
c) A seal (round) including the attached bee and logo included in the Zip file.
Do note that a) & b) can also be combined into one design as long as the symmetry on the jar stays intact.

The final design should communicate modern aesthetics, high quality, that are slightly provocative and pop off the shelves.

Hi folks, sorry for the delay in completing this project, but my business partner had a leak in his house. We planned to finalise our review today, but this will have to wait until it's no longer raining in his livingroom. Our sincere apologies!

• See branding guidelines

• Must follow the branding guideline and fonts provided as attachment

```html
<!DOCTYPE html>
<html lang="en">
<head>
<meta charset="utf-8">
<title>Honey Plinks – Jar Label</title>
<link href="https://fonts.googleapis.com/css2?family=Lato:wght@400;700;900&display=swap" rel="stylesheet">
<style>
  :root {
    --page-bg: #f2f2f2;
    --comb-dark: #2f1e12;
    --gold-edge: #f6b20c;
    --gold-mid: #fbd10a;
    --gold-bright: #fff200;
    --ink: #0d0d0d;
    --paper: #ffffff;
  }
  html, body {
    margin: 0;
    padding: 0;
    width: 1200px;
    height: 1070px;
    overflow: hidden;
    background: var(--page-bg);
    font-family: "Lato", Arial, sans-serif;
  }
  .canvas {
    position: relative;
    width: 1200px;
    height: 1070px;
  }
  .label-sheet {
    position: absolute;
    left: 80px;
    top: 371px;
    width: 1040px;
    height: 328px;
  }
  .label-sheet text { font-family: "Lato", Arial, sans-serif; }
  .brand-name { font-weight: 900; font-size: 52px; fill: var(--ink); }
  .honey-type { font-weight: 400; font-size: 35px; fill: var(--paper); }
  .origin { font-weight: 400; font-size: 29px; fill: var(--ink); }
  .side-copy { font-weight: 400; font-size: 23px; fill: var(--ink); }
</style>
</head>
<body>
<main class="canvas">
  <svg class="label-sheet" viewBox="0 0 1300 410" xmlns="http://www.w3.org/2000/svg">
    <defs>
      <linearGradient id="goldBand" x1="0" x2="1" y1="0" y2="0">
        <stop offset="0" stop-color="var(--gold-edge)"/>
        <stop offset="0.5" stop-color="var(--gold-bright)"/>
        <stop offset="1" stop-color="var(--gold-edge)"/>
      </linearGradient>
      <radialGradient id="goldBadge" cx="0.5" cy="0.45" r="0.6">
        <stop offset="0" stop-color="var(--gold-bright)"/>
        <stop offset="1" stop-color="var(--gold-mid)"/>
      </radialGradient>
    </defs>

    <!-- label bands -->
    <rect class="comb-band" x="0" y="40" width="1300" height="163" fill="var(--comb-dark)" role="img" aria-label="Dark honeycomb pattern band"/>
    <rect class="gold-band" x="0" y="203" width="1300" height="164" fill="url(#goldBand)"/>
    <rect class="paper-band" x="0" y="367" width="1300" height="43" fill="var(--paper)"/>

    <!-- back panel copy -->
    <g class="back-panel" text-anchor="middle">
      <text class="side-copy" x="199" y="244">Unsuitable for children</text>
      <text class="side-copy" x="199" y="273">under 12 months</text>
      <line x1="66" y1="292" x2="332" y2="292" stroke="var(--ink)" stroke-width="3"/>
      <text class="side-copy" x="199" y="328">Limited edition No. X / 100</text>
    </g>

    <!-- front badge -->
    <g class="front-badge">
      <polygon points="530,0 770,0 885,203 770,408 530,408 415,203" fill="var(--gold-mid)"/>
      <polygon points="533,5 767,5 879,203 767,403 533,403 421,203" fill="var(--ink)"/>
      <polygon points="560,30 740,30 830,188 470,188" fill="url(#goldBadge)"/>
      <polygon points="475,250 825,250 752,378 548,378" fill="url(#goldBadge)"/>
      <g text-anchor="middle">
        <text class="brand-name" x="650" y="105">HONEY</text>
        <text class="brand-name" x="650" y="163">PLINKS</text>
        <text class="honey-type" x="650" y="233">RAW HONEY</text>
        <text class="origin" x="650" y="301">EU HONEY</text>
        <text class="origin" x="650" y="336">SINGLE ORGIN</text>
      </g>
    </g>

    <!-- side panel copy -->
    <g class="side-panel" text-anchor="middle">
      <text class="side-copy" x="1104" y="244">The appropriate</text>
      <text class="side-copy" x="1104" y="273">durability declaration</text>
      <line x1="971" y1="292" x2="1237" y2="292" stroke="var(--ink)" stroke-width="3"/>
      <text class="side-copy" x="1104" y="328">Net Weight (250g)</text>
    </g>
  </svg>
</main>
</body>
</html>
```